Heartwood Builders Business Card Design

We need a business card for an established builder of high quality bespoke homes in Auckland and Northland. We build and renovate homes collaboratively facilitating effective communication between owners, builders, architects, suppliers and tradespeople. We have never built or renovated a home that leaks or has faults. We only use reliable materials. We have never been sued or had legal action taken against us. We are honest builders of bespoke homes not group mass produced homes. Our niche market is in character homes. We practice sustainability and have built a lot of coastal property. We have been in business for over thirty years . We would like to see natural colors of the environment sand,sea and maybe vegetation . The design should communicate quality, sustainability,fair pricing, open communication and the originality of bespoke building. And the fact that the builder is registered.

Industry/Entity Type

Business

Contact Information for Business Card

Rowan Tellick Builders
Ph. 021583917
18 Kestrel Rd Harwood Bay Auckland 0814
PO Box 927 Mangawhai 0583

```html
<!DOCTYPE html>
<html lang="en">
<head>
<meta charset="utf-8">
<title>Heartwood Builders Business Card</title>
<link href="https://fonts.googleapis.com/css2?family=Open+Sans:wght@400;600;800&display=swap" rel="stylesheet">
<style>
  :root {
    --brand-red: #b10000;
    --accent-red: #c0141b;
    --ink: #2b2b2b;
    --paper: #ffffff;
    --backdrop: #ecebe8;
    --card-shadow: rgba(0, 0, 0, 0.18);
  }
  * { margin: 0; padding: 0; box-sizing: border-box; }
  html, body {
    width: 1200px;
    height: 900px;
    overflow: hidden;
    background: var(--backdrop);
    font-family: "Open Sans", Arial, sans-serif;
  }
  .canvas {
    position: relative;
    width: 1200px;
    height: 900px;
  }
  .card {
    position: absolute;
    width: 560px;
    height: 320px;
    box-shadow: 0 10px 28px var(--card-shadow);
  }
  .card--front {
    left: 120px;
    top: 110px;
    background: var(--brand-red);
    display: flex;
    align-items: center;
    justify-content: center;
  }
  .card--back {
    left: 520px;
    top: 470px;
    background: var(--paper);
  }
  .brand-name {
    font-weight: 800;
    letter-spacing: 0.5px;
    display: flex;
    align-items: center;
    gap: 12px;
  }
  .brand-name__mark {
    width: 14px;
    height: 14px;
  }
  .card--front .brand-name {
    color: var(--paper);
    font-size: 46px;
  }
  .card--front .brand-name__mark { background: var(--paper); width: 18px; height: 18px; }
  .card--back .brand-name {
    position: absolute;
    left: 34px;
    top: 70px;
    color: var(--ink);
    font-size: 28px;
  }
  .card--back .brand-name__mark { background: var(--accent-red); }
  .contact {
    position: absolute;
    left: 330px;
    top: 120px;
    color: var(--ink);
    font-size: 13px;
    line-height: 1.45;
  }
  .contact__name {
    color: var(--accent-red);
    font-weight: 600;
    font-size: 16px;
    margin-bottom: 14px;
  }
  .contact__phone {
    display: flex;
    align-items: center;
    gap: 6px;
    margin-bottom: 12px;
  }
  .contact__phone svg { width: 11px; height: 11px; fill: var(--accent-red); }
</style>
</head>
<body>
<main class="canvas">
  <section class="card card--front" aria-label="Card front">
    <div class="brand-name"><span class="brand-name__mark"></span>Heartwood Builders</div>
  </section>

  <section class="card card--back" aria-label="Card back">
    <div class="brand-name"><span class="brand-name__mark"></span>Heartwood Builders</div>
    <address class="contact" style="font-style: normal;">
      <p class="contact__name">Rowan Tellick Builders</p>
      <p class="contact__phone">
        <svg viewBox="0 0 24 24" aria-hidden="true"><path d="M6.6 10.8a15.1 15.1 0 0 0 6.6 6.6l2.2-2.2a1 1 0 0 1 1-.25 11.4 11.4 0 0 0 3.6.57 1 1 0 0 1 1 1V20a1 1 0 0 1-1 1A17 17 0 0 1 3 4a1 1 0 0 1 1-1h3.5a1 1 0 0 1 1 1c0 1.25.2 2.45.57 3.57a1 1 0 0 1-.25 1z"/></svg>
        021583917
      </p>
      <p>18 Kestrel Rd Harwood</p>
      <p>Bay Auckland 0814</p>
      <p>PO Box 927 Mangawhai 0583</p>
    </address>
  </section>
</main>
</body>
</html>
```